Penny Harvest

Logo and general packaging design for premium quality, price conscious super foods.

Initial product portfolio includes:

Organic Raw Chia Seeds - Resealable plastic bags with 3 x 5 label.
Organic Cold Pressed Coconut Oil (plastic jar) - 2.5 x 6.5 label

The design should be transferable to additional products.

Project requirements:

The design should be simple and the core trade dress should be no more than 2 or 3 colors. The logo should reproduce well in black/1 color.

The idea of this design is to convey quality and simplicity, like a "no frills", premium quality brand.

Deliverable: fully editable (text and illustration):

Logo.

Basic Jar label design.

Basic Bag label design.

Target Market(s)

Educated women aged 22-45

Industry/Entity Type

Plastic

Requirements
Must have
• Clear, simple logo, delivered in vector form, 1 color/black.
• Use of logo on 1 jar label and 1 bag label, each with product name and space for required and optional marketing content.
Nice to have
• Additional iterations of the design to demonstrate your concept of how we will visually vary additional items in jars and bags.
• i.e. What an additional product in a bag would look like for purposes of brand consistency and product differentiation on shelf or online in e-store.
Should not have
• overly detailed graphics that don't scale well and/or may be hard to read or understand. 4 color design elements (except to simiulate how the product may look through the clear jar or bag or how the product may be placed in a simulated surrounding or ad.

```html
<!DOCTYPE html>
<html lang="en">
<head>
<meta charset="utf-8">
<title>Penny Harvest – Organic Raw Chia Seeds labels</title>
<link rel="stylesheet" href="https://fonts.googleapis.com/css2?family=Barlow:wght@300;400;700&display=swap">
<style>
  :root {
    --backdrop: #e4edcd;
    --leaf-green: #79ad2d;
    --deep-green: #0f5a2e;
    --tag-green: #74a92b;
    --paper: #ffffff;
  }
  html, body {
    margin: 0;
    width: 1200px;
    height: 1200px;
    overflow: hidden;
    background: var(--backdrop);
    font-family: "Barlow", sans-serif;
  }
  .canvas { position: relative; width: 1200px; height: 1200px; }
  .label { position: absolute; display: block; }
  .label--white { left: 158px; top: 100px; width: 522px; height: 905px; }
  .label--green { left: 698px; top: 197px; width: 395px; height: 685px; }
  .brand-name { font-family: "Barlow", sans-serif; font-weight: 700; font-size: 40px; }
  .title-light { font-family: "Barlow", sans-serif; font-weight: 300; }
  .title-bold { font-family: "Barlow", sans-serif; font-weight: 700; }
  .weight { font-family: "Barlow", sans-serif; font-weight: 400; font-size: 32px; }
  .claims { font-family: "Barlow", sans-serif; font-weight: 400; font-size: 19px; letter-spacing: 1px; }
</style>
</head>
<body>
<main class="canvas">

  <!-- Bag label, white edition -->
  <svg class="label label--white" viewBox="0 0 522 905" xmlns="http://www.w3.org/2000/svg">
    <defs>
      <linearGradient id="plant-tone-a" x1="0" y1="0" x2="0" y2="1">
        <stop offset="0" stop-color="#1d6a36"/>
        <stop offset="0.6" stop-color="#4f4f7a"/>
        <stop offset="1" stop-color="#8a3b96"/>
      </linearGradient>
    </defs>
    <rect class="label-ground" width="522" height="905" fill="var(--paper)"/>
    <path class="leaf" fill="var(--leaf-green)"
      d="M50 0 L497 0 C512 150 502 320 425 425 C375 490 300 530 272 560 C245 525 170 490 115 425 C40 330 35 150 50 0 Z"/>
    <circle class="brand-dot" cx="272" cy="78" r="20" fill="var(--paper)"/>
    <text class="brand-name" x="272" y="140" text-anchor="middle" fill="var(--paper)">Penny</text>
    <text class="brand-name" x="272" y="180" text-anchor="middle" fill="var(--paper)">Harvest</text>
    <rect class="plant-illustration" role="img" aria-label="Illustration of a flowering chia plant stalk with purple blossoms"
      x="215" y="210" width="100" height="380" rx="45" fill="url(#plant-tone-a)" opacity="0.8"/>
    <circle class="organic-badge" cx="418" cy="530" r="50" fill="none" stroke="var(--leaf-green)" stroke-width="3"/>
    <text class="title-light" x="47" y="670" font-size="100" textLength="445" lengthAdjust="spacingAndGlyphs" fill="var(--deep-green)">ORGANIC</text>
    <text class="title-bold" x="47" y="748" font-size="92" textLength="450" lengthAdjust="spacingAndGlyphs" fill="var(--deep-green)">RAW CHIA</text>
    <line class="rule" x1="52" y1="776" x2="172" y2="776" stroke="var(--deep-green)" stroke-width="2"/>
    <text class="weight" x="52" y="822" fill="var(--deep-green)">300gm</text>
    <text class="title-light" x="200" y="822" font-size="88" textLength="292" lengthAdjust="spacingAndGlyphs" fill="var(--deep-green)">SEEDS</text>
    <text class="claims" x="52" y="860" textLength="440" lengthAdjust="spacingAndGlyphs" fill="var(--tag-green)">NO CHOLESTEROL•RICH IN ANTIOXIDANTS</text>
  </svg>

  <!-- Bag label, green edition -->
  <svg class="label label--green" viewBox="0 0 522 905" xmlns="http://www.w3.org/2000/svg">
    <defs>
      <linearGradient id="plant-tone-b" x1="0" y1="0" x2="0" y2="1">
        <stop offset="0" stop-color="#1d6a36"/>
        <stop offset="0.6" stop-color="#4f4f7a"/>
        <stop offset="1" stop-color="#8a3b96"/>
      </linearGradient>
    </defs>
    <rect class="label-ground" width="522" height="905" fill="var(--leaf-green)"/>
    <path class="leaf" fill="var(--paper)"
      d="M50 0 L497 0 C512 150 502 320 425 425 C375 490 300 530 272 560 C245 525 170 490 115 425 C40 330 35 150 50 0 Z"/>
    <circle class="brand-dot" cx="272" cy="78" r="20" fill="var(--leaf-green)"/>
    <text class="brand-name" x="272" y="140" text-anchor="middle" fill="var(--leaf-green)">Penny</text>
    <text class="brand-name" x="272" y="180" text-anchor="middle" fill="var(--leaf-green)">Harvest</text>
    <rect class="plant-illustration" role="img" aria-label="Illustration of a flowering chia plant stalk with purple blossoms"
      x="215" y="210" width="100" height="380" rx="45" fill="url(#plant-tone-b)" opacity="0.8"/>
    <circle class="organic-badge" cx="418" cy="530" r="50" fill="none" stroke="var(--deep-green)" stroke-width="3"/>
    <text class="title-light" x="47" y="670" font-size="100" textLength="445" lengthAdjust="spacingAndGlyphs" fill="var(--paper)">ORGANIC</text>
    <text class="title-bold" x="47" y="748" font-size="92" textLength="450" lengthAdjust="spacingAndGlyphs" fill="var(--paper)">RAW CHIA</text>
    <line class="rule" x1="52" y1="776" x2="172" y2="776" stroke="var(--paper)" stroke-width="2"/>
    <text class="weight" x="52" y="822" fill="var(--paper)">300gm</text>
    <text class="title-light" x="200" y="822" font-size="88" textLength="292" lengthAdjust="spacingAndGlyphs" fill="var(--paper)">SEEDS</text>
    <text class="claims" x="52" y="860" textLength="440" lengthAdjust="spacingAndGlyphs" fill="var(--deep-green)">NO CHOLESTEROL•RICH IN ANTIOXIDANTS</text>
  </svg>

</main>
</body>
</html>
```